Business Card Design for Flood Rescue 360 - Property Restoration Professionals

I need a business card designed for Flood Rescue 360. We are a full-service property restoration solution. Providing water, fire, smoke & storm restoration as well as mold remediation and full remodel or reconstruction to homes and businesses across Dallas-Fort Worth, TX.
Target Market(s)
home and business owners with insurance covered property damage from water, fire or storm related damage
Industry/Entity Type
property restoration
Contact Information for Business Card
Marcus Pelley General Manager Cell: 214-555-0193 Office: 469-555-0148 email: Marcus@FloodRescue360.example services: Water, Fire, Mold, Reconstruction Tagline: Urgency for Your Water Emergency!
Look and feel
Each slider illustrates characteristics of the customer's brand and the style your logo design should communicate.

```html
<!DOCTYPE html>
<html lang="en">
<head>
<meta charset="utf-8">
<title>Flood Rescue 360 – Business Card</title>
<link href="https://fonts.googleapis.com/css2?family=Roboto:wght@400;500;700;900&family=Roboto+Condensed:wght@400;700&display=swap" rel="stylesheet">
<style>
  :root {
    --stage: #121212;
    --brand-blue: #19b4e5;
    --white: #ffffff;
    --ink: #1c1c1c;
    --grey: #6f6f6f;
    --faint: #eef3f6;
  }
  * { margin: 0; padding: 0; box-sizing: border-box; }
  html, body { width: 1200px; height: 960px; overflow: hidden; }
  body {
    background: var(--stage);
    font-family: "Roboto", Arial, sans-serif;
    position: relative;
  }
  .card {
    position: absolute;
    left: 249px;
    width: 702px;
    height: 401px;
    overflow: hidden;
    box-shadow: 0 14px 30px rgba(0,0,0,.55);
  }
  /* Front */
  .card-front { top: 60px; background: var(--brand-blue); color: var(--white); }
  .front-wordmark {
    position: absolute;
    left: 118px; top: 118px;
    width: 470px;
    font-weight: 900;
    font-size: 70px;
    line-height: 0.98;
    letter-spacing: -1px;
    text-transform: uppercase;
  }
  .services {
    position: absolute;
    left: 0; right: 0; top: 330px;
    text-align: center;
  }
  .services-heading {
    display: flex; align-items: center; justify-content: center; gap: 8px;
    font-size: 17px; font-weight: 500; letter-spacing: .3px;
  }
  .services-heading::before, .services-heading::after {
    content: ""; width: 122px; height: 2px;
    background: linear-gradient(90deg, rgba(255,255,255,.3), var(--white));
  }
  .services-heading::after { background: linear-gradient(90deg, var(--white), rgba(255,255,255,.3)); }
  .services-list {
    margin-top: 6px;
    display: flex; justify-content: center; gap: 7px;
    list-style: none; font-size: 17px; letter-spacing: .4px;
  }
  .services-list li { display: flex; align-items: center; gap: 6px; }
  .services-list li::before {
    content: ""; width: 10px; height: 10px; border-radius: 50%;
    border: 2px solid var(--white);
  }
  /* Back */
  .card-back { top: 500px; background: var(--white); }
  .back-decoration {
    position: absolute; left: 432px; top: 78px;
    width: 268px; height: 268px; border-radius: 50%;
    border: 20px solid var(--faint);
  }
  .back-wordmark {
    position: absolute; left: 27px; top: 22px;
    width: 330px;
    color: var(--brand-blue);
    font-weight: 900; font-size: 50px; line-height: 1.02;
    letter-spacing: -1px; text-transform: uppercase;
  }
  .person {
    position: absolute; right: 30px; top: 168px; text-align: right;
  }
  .person-name {
    font-family: "Roboto Condensed", Arial, sans-serif;
    font-size: 38px; line-height: 1;
  }
  .person-first { color: var(--brand-blue); font-weight: 700; }
  .person-last { color: var(--grey); font-weight: 400; }
  .person-title { font-size: 18px; color: var(--ink); margin-top: 3px; font-weight: 500; }
  .accent-bar {
    position: absolute; right: 0; top: 168px; width: 20px; height: 62px;
    background: var(--brand-blue);
  }
  .tagline {
    position: absolute; left: 29px; top: 258px;
    color: var(--brand-blue); font-size: 17.5px; letter-spacing: .3px;
  }
  .contacts {
    position: absolute; left: 24px; top: 308px; list-style: none;
  }
  .contacts li {
    display: flex; align-items: center; gap: 8px;
    font-size: 17.5px; color: var(--ink); letter-spacing: .6px; height: 23.5px;
  }
  .contacts svg { width: 15px; height: 15px; flex: none; }
</style>
</head>
<body>
  <section class="card card-front" aria-label="Card front">
    <div class="front-wordmark">Flood Rescue 360</div>
    <div class="services">
      <div class="services-heading">SERVICES</div>
      <ul class="services-list">
        <li>Water</li><li>Fire</li><li>Mold</li><li>Reconstruction</li>
      </ul>
    </div>
  </section>

  <section class="card card-back" aria-label="Card back">
    <div class="back-decoration"></div>
    <div class="back-wordmark">Flood Rescue 360</div>
    <div class="person">
      <div class="person-name"><span class="person-first">Marcus</span> <span class="person-last">Pelley</span></div>
      <div class="person-title">General Manager</div>
    </div>
    <div class="accent-bar"></div>
    <p class="tagline">Urgency for Your Water Emergency!</p>
    <ul class="contacts">
      <li>
        <svg viewBox="0 0 16 16" aria-hidden="true"><rect x="4" y="1" width="8" height="14" rx="1.5" fill="none" stroke="#19b4e5" stroke-width="1.6"/><line x1="7" y1="12.5" x2="9" y2="12.5" stroke="#19b4e5" stroke-width="1.4"/></svg>
        214-555-0193
      </li>
      <li>
        <svg viewBox="0 0 16 16" aria-hidden="true"><path d="M3.5 1.5l2.5 3-1.5 1.8c.8 1.9 2.3 3.4 4.2 4.2L10.5 9l3 2.5-1.3 2.5C7 14 2 9 2 3.2z" fill="#19b4e5"/><path d="M9 2.5a4.5 4.5 0 0 1 4.5 4.5M9 5a2 2 0 0 1 2 2" fill="none" stroke="#19b4e5" stroke-width="1.2"/></svg>
        469-555-0148
      </li>
      <li>
        <svg viewBox="0 0 16 16" aria-hidden="true"><path d="M1 6.5L8 2l7 4.5V15H1z" fill="#19b4e5"/><path d="M1 7l7 4.5L15 7" fill="none" stroke="#fff" stroke-width="1.2"/></svg>
        Marcus@FloodRescue360.example
      </li>
    </ul>
  </section>
</body>
</html>
```